Restaurant Facility Equipment & Store Maintenance/

I need a flyer showing commercial/industrial kitchen equipment photos we work on Hot Equipment & Cold Equipment and offer many services. see attached highlights

```html
<!DOCTYPE html>
<html lang="en">
<head>
<meta charset="utf-8">
<title>Restaurant Facility Equipment &amp; Store Maintenance Flyer</title>
<link href="https://fonts.googleapis.com/css2?family=Red+Hat+Display:wght@400;500;700;800&display=swap" rel="stylesheet">
<style>
  :root {
    --backdrop: #9b9b9e;
    --navy: #1d2a42;
    --orange: #f15a22;
    --red: #e8262b;
    --blue: #3b6fc4;
    --ink: #1f2a44;
    --paper: #ffffff;
    --frame: #c4502a;
    --rule: #b9bcc4;
  }
  * { margin: 0; padding: 0; box-sizing: border-box; }
  html, body {
    width: 1200px;
    height: 2678px;
    overflow: hidden;
    background: var(--backdrop);
    font-family: "Red Hat Display", Arial, sans-serif;
  }
  .flyer {
    position: absolute;
    left: 50px;
    top: 569px;
    width: 1100px;
    height: 1540px;
    background: var(--paper);
    overflow: hidden;
  }
  .hero-photo {
    position: absolute;
    left: 0; top: 0;
    width: 1100px; height: 734px;
    background:
      radial-gradient(ellipse at 55% 72%, rgba(150,160,175,0.45), transparent 55%),
      linear-gradient(180deg, #0f1626 0%, #25303f 45%, #3a4350 70%, #1a2230 100%);
  }
  .hero-frame {
    position: absolute;
    left: 77px; top: 35px;
    width: 946px; height: 720px;
    border: 1.5px solid var(--frame);
    border-bottom: none;
  }
  .headline {
    position: absolute;
    left: 0; top: 64px;
    width: 1100px;
    text-align: center;
    color: #fff;
    font-weight: 700;
    font-size: 43px;
    line-height: 49px;
    white-space: nowrap;
  }
  .tagline-band {
    position: absolute;
    left: 77px; top: 734px;
    width: 946px; height: 62px;
    background: var(--orange);
    color: #fff;
    font-weight: 700;
    font-size: 29px;
    line-height: 62px;
    text-align: center;
    white-space: nowrap;
  }
  .intro {
    position: absolute;
    left: 0; top: 826px;
    width: 1100px;
    text-align: center;
    color: var(--ink);
    font-weight: 400;
    font-size: 18.5px;
    line-height: 24px;
    white-space: nowrap;
  }
  .service-list {
    position: absolute;
    list-style: none;
    color: var(--ink);
    font-weight: 400;
    font-size: 22px;
    line-height: 28px;
    border-left: 1.5px solid var(--rule);
    white-space: nowrap;
  }
  .service-list li {
    position: relative;
    padding-left: 28px;
    margin-bottom: 10px;
  }
  .service-list li:last-child { margin-bottom: 0; }
  .service-list li::before {
    content: "";
    position: absolute;
    left: -4px; top: 11px;
    width: 6px; height: 6px;
    border-radius: 50%;
    background: var(--red);
  }
  .service-list.left { left: 84px; top: 929px; width: 460px; }
  .service-list.right { left: 574px; top: 929px; width: 440px; }
  .warranty {
    position: absolute;
    left: 87px; top: 1306px;
    width: 408px; height: 234px;
    background: var(--navy);
  }
  .warranty-days {
    position: absolute;
    left: 0; top: 0; width: 408px;
    text-align: center;
    color: var(--red);
    font-weight: 800;
    font-size: 96px;
    line-height: 106px;
  }
  .warranty-band {
    position: absolute;
    left: 74px; top: 1414px;
    width: 433px; height: 65px;
    background: var(--orange);
    color: #fff;
    font-weight: 700;
    font-size: 58px;
    line-height: 66px;
    text-align: center;
    letter-spacing: 3px;
  }
  .warranty-note {
    position: absolute;
    left: 87px; top: 1489px;
    width: 408px;
    text-align: center;
    color: #fff;
    font-weight: 400;
    font-size: 23px;
    line-height: 30px;
    white-space: nowrap;
  }
  .base-rule {
    position: absolute;
    left: 495px; top: 1534px;
    width: 605px; height: 6px;
    background: var(--blue);
  }
  .mascot {
    position: absolute;
    left: 882px; top: 1254px;
    width: 212px; height: 280px;
    border-radius: 40px 40px 10px 10px;
    background: linear-gradient(160deg, #f08a3c 0%, #e56a2a 45%, #3e64b0 100%);
    opacity: 0.9;
  }
</style>
</head>
<body>
  <main class="flyer">
    <div class="hero-photo" role="img" aria-label="Photo of a dim commercial restaurant kitchen with stainless steel counters, pots and pans"></div>
    <div class="hero-frame"></div>
    <h1 class="headline">Installation, Rebuilds, OSHA<br>Inspection, and Preventive Maintenance<br>Services for Denver Metro and<br>Surrounding Areas.</h1>

    <div class="tagline-band">We handle everything from the front door to the back door</div>

    <p class="intro">We offer hot and cold equipment repair, cleaning, maintenance, handyman work, drywall, painting,<br>door closers, floors, and ceiling tiles. For any need in your restaurant, call us and we will send a<br>skilled technician to manage all your commercial and industrial facility requirements.</p>

    <ul class="service-list left">
      <li>CKESA Certified Technicians</li>
      <li>Round-the-clock emergency services</li>
      <li>Customers who subscribe to<br>preventive maintenance services<br>receive a reduced rate on hourly<br>labor charges.</li>
      <li>Original equipment manufacturer<br>(OEM) parts</li>
      <li>Equipment Cleaning &amp; Rebuilds</li>
      <li>Used equipment available for<br>purchase or rental</li>
    </ul>

    <ul class="service-list right">
      <li>Specialized Programs for Preventive<br>Maintenance of Equipment</li>
      <li>Installation and Repair of Restaurant<br>Equipment</li>
      <li>Repair or replace restaurant furniture</li>
      <li>Comprehensive licensed electrical<br>contractor services for both interior<br>and exterior projects, including<br>lighting system upgrades.</li>
      <li>Building Graffiti Removal Services</li>
      <li>Hot &amp; Cold Equipment</li>
      <li>Food Service Trucks</li>
      <li>We repair floors, walls,<br>counters, décor, signage,<br>parking lots, dumpsters,<br>and more. If you have it,<br>we probably fix it.</li>
    </ul>

    <div class="warranty">
      <div class="warranty-days">30-DAY</div>
    </div>
    <div class="warranty-band">WARRANTY</div>
    <div class="warranty-note">ON ALL OEM PARTS INSTALLED</div>

    <div class="base-rule"></div>
    <div class="mascot" role="img" aria-label="Cartoon handyman mascot in orange shirt and blue overalls holding a wrench and giving a thumbs up"></div>
  </main>
</body>
</html>
```